Manuka Honey company needs a Upmarket, Luxury Website!

New Zealand, Taranaki based Manuka Honey company Rimu Vale Honey is looking for a new website, we are looking for an upmarket, luxury, serious website design. We export the highest quality quality Manuka Honey, straight from the Taranaki region.

Main export markets are Asia & Europe, also New Zealand & Australia.

Looking to have a beautiful, upmarket, serious, luxurious & graphical experience with mobile optimization in mind. Like the use of product staging/mockups

You can use copy from other websites to build the site and we will change the copy after the design is finished.

***Please include 'Honey Product' mockups in website.

*Will add illustrator files in coming days***

Feel free to make website functional in Shopify, Wordpress or WIX

Target Market(s)

Asia, Europe (main markets) New Zealand, Australia (Submarkets)

Coding

Coded - Design and coding required

Number of Pages Required

4 page

Requirements
Must have
• Home, Shop, About Us, Contact Us

Homepage to include:

Our Products
Company Video (video under construction)
What is MGO/KPS
Newsletter Opt-in

***(Not in Order)***

Please include 'Honey Product' mockups in website.
*Will add illustrator files in coming days
Nice to have
• FAQ & Partnership Inquiries (hyperlink in footer)

```html
<!DOCTYPE html>
<html lang="en">
<head>
<meta charset="utf-8">
<title>Rimu Vale Honey</title>
<link rel="stylesheet" href="https://fonts.googleapis.com/css2?family=Poppins:wght@400;500;600;700&display=swap">
<style>
:root{
  --bg-dark:#2b2b2b;
  --bg-mid:#363636;
  --bg-card:#3f3f3f;
  --bg-footer:#333333;
  --gold:#d4b85a;
  --gold-light:#f3e79a;
  --gold-deep:#c4a04c;
  --white:#ffffff;
  --text-light:#d8d8d8;
  --text-dark:#2a2a2a;
  --text-muted:#6a6a6a;
  --price:#6fa52b;
  --line:#555555;
}
*{margin:0;padding:0;box-sizing:border-box}
html,body{width:1200px;height:4172px;overflow:hidden}
body{position:relative;background:var(--bg-dark);font-family:'Poppins',sans-serif;color:var(--white)}
.abs{position:absolute}
.photo{position:absolute}

/* header & hero */
.hero-side{left:568px;top:0;width:632px;height:810px;background:var(--bg-mid)}
.brand{left:87px;top:52px;display:flex;align-items:center;gap:12px}
.brand-mark{width:44px;height:44px;border-radius:50%;border:2px solid var(--gold)}
.brand-name{font-size:15px;font-weight:600;color:var(--gold)}
.nav{top:66px;left:662px;font-size:12.5px;font-weight:500;letter-spacing:.2px}
.nav a{color:var(--white);text-decoration:none;position:absolute;white-space:nowrap}
.header-icons{top:62px;left:1015px;display:flex;gap:14px}
.cart-badge{position:absolute;left:86px;top:-2px;width:14px;height:14px;border-radius:50%;background:var(--gold);color:var(--text-dark);font-size:9px;font-weight:700;text-align:center;line-height:14px}
.hero-kicker{left:87px;top:238px;font-size:14px;font-weight:700}
.hero-title{left:87px;top:262px;font-size:45px;font-weight:700;line-height:46px;white-space:nowrap}
.hero-text{left:87px;top:414px;font-size:13.5px;line-height:23px;width:360px;color:var(--text-light)}
.btn-gold{left:87px;top:481px;width:139px;height:45px;border-radius:23px;background:linear-gradient(90deg,var(--gold-light),var(--gold-deep));color:var(--text-dark);font-size:13px;font-weight:700;display:flex;align-items:center;justify-content:center}
.vline{width:2px;background:var(--gold)}

/* about */
.about-band{left:0;top:810px;width:1200px;height:607px;background:linear-gradient(90deg,var(--gold-light) 0%,#e6cf7a 50%,var(--gold-deep) 100%)}
.frame-white{background:var(--white)}
.about-card{left:559px;top:931px;width:552px;height:369px;background:var(--white);color:var(--text-dark)}
.about-title{left:59px;top:54px;font-size:36px;font-weight:600;white-space:nowrap}
.about-rule{left:40px;top:104px;width:65px;height:2px;background:#9a9a9a}
.about-text{left:59px;top:136px;width:450px;font-size:13.5px;line-height:20.5px;color:var(--text-muted)}
.btn-grey{left:59px;top:270px;width:127px;height:37px;border-radius:19px;background:#e5e5e5;color:var(--text-dark);font-size:12.5px;font-weight:700;display:flex;align-items:center;justify-content:center}

/* products */
.section-title{width:1200px;left:0;text-align:center;font-size:45px;font-weight:700}
.product{top:1773px;width:238px;height:283px;background:var(--bg-card);text-align:center}
.jar{position:absolute;left:68px;top:-60px;width:102px;height:189px;border-radius:18px 18px 14px 14px;background:linear-gradient(180deg,#3a3a3a 0 10%,#f2a216 10%,#e88e0c 100%)}
.product-name{position:absolute;top:147px;left:0;width:100%;font-size:16px;font-weight:700;line-height:21px}
.stars{position:absolute;top:191px;left:0;width:100%;font-size:18px;letter-spacing:2px;color:var(--gold)}
.stars .off{color:#9a9a9a}
.product-rule{position:absolute;top:235px;left:16px;width:206px;height:1px;background:var(--line)}
.price{position:absolute;top:246px;left:0;width:100%;font-size:14px;font-weight:600}
.price b{color:var(--price);font-size:18px;font-weight:600}

/* mgo */
.mgo-card{left:87px;top:2399px;width:583px;height:366px;background:var(--bg-card)}
.vs{left:132px;top:2352px;width:76px;height:76px;border-radius:50%;background:radial-gradient(circle at 35% 35%,var(--gold-light),var(--gold-deep));color:var(--white);font-size:28px;font-weight:700;display:flex;align-items:center;justify-content:center}
.mgo-heading{left:44px;top:62px;font-size:22px;font-weight:600;white-space:nowrap}
.mgo-text{left:44px;top:106px;width:490px;font-size:13.5px;line-height:20.5px;color:var(--text-light)}
.grade-table{position:absolute;left:44px;top:160px;width:322px;border-collapse:collapse;font-size:13.5px;font-weight:600}
.grade-table td{height:34px;border-bottom:1px solid var(--line);padding:0}
.grade-table tr:last-child td{border-bottom:none}
.grade-table td:first-child{width:160px}
.arrow-btn{width:42px;height:42px;border-radius:50%;border:1.5px solid #8a8a8a;display:flex;align-items:center;justify-content:center}
.slider-rule{left:225px;top:2857px;width:238px;height:1px;background:#555}

/* video */
.play{left:521px;top:3249px;width:98px;height:98px;border-radius:50%;background:radial-gradient(circle at 35% 35%,var(--gold-light),var(--gold-deep));display:flex;align-items:center;justify-content:center}
.video-title{left:652px;top:3180px;font-size:36px;font-weight:600;white-space:nowrap}
.video-text{left:652px;top:3257px;width:465px;font-size:14.5px;line-height:22px;color:var(--text-light)}

/* newsletter & footer */
.footer-bg{left:0;top:3732px;width:1200px;height:440px;background:var(--bg-footer)}
.newsletter{left:594px;top:3656px;width:606px;height:149px;background:linear-gradient(90deg,#e8d37c,var(--gold-deep))}
.newsletter-label{left:36px;top:38px;font-size:11.5px;font-weight:600;color:var(--text-dark)}
.newsletter-field{left:36px;top:65px;width:479px;height:44px;background:var(--white);display:flex;align-items:center;padding-left:16px;gap:8px;font-size:14.5px;color:#9a9a9a}
.subscribe{position:absolute;right:5px;top:4px;width:116px;height:36px;background:#1e1e1e;color:var(--white);font-size:11.5px;font-weight:700;display:flex;align-items:center;justify-content:center}
.footer-brand{left:215px;top:3884px;width:140px;height:140px;border-radius:50%;border:2px solid var(--gold);display:flex;align-items:center;justify-content:center;text-align:center;font-size:15px;font-weight:600;color:var(--gold);line-height:20px}
.footer-col h4{font-size:15px;font-weight:700;margin-bottom:14px}
.footer-col a{display:block;color:var(--text-light);text-decoration:none;font-size:13px}
.social{width:34px;height:34px;border-radius:50%;background:#4a4a4a}
.footer-rule{left:0;top:4115px;width:1200px;height:1px;background:#474747}
.copyright{left:0;top:4136px;width:1200px;text-align:center;font-size:11.5px;font-weight:500;color:var(--text-light)}
.to-top{left:1129px;top:4091px;width:42px;height:42px;border-radius:50%;background:var(--gold);display:flex;align-items:center;justify-content:center}
</style>
</head>
<body>

<!-- Header / hero -->
<div class="abs hero-side"></div>

<div class="abs brand"><span class="brand-mark"></span><span class="brand-name">Rimu Vale Honey</span></div>

<nav class="abs nav">
  <a style="left:0">HOME</a>
  <a style="left:67px">SHOP</a>
  <a style="left:130px">ABOUT US</a>
  <a style="left:224px">CONTACT US</a>
</nav>
<div class="abs header-icons">
  <svg width="20" height="20" viewBox="0 0 20 20" fill="none" stroke="#fff" stroke-width="1.5"><circle cx="10" cy="6" r="4"/><path d="M3 19c0-4 3-6 7-6s7 2 7 6"/></svg>
  <svg width="20" height="20" viewBox="0 0 20 20" fill="none" stroke="#fff" stroke-width="1.5"><circle cx="8.5" cy="8.5" r="6"/><path d="M13 13l5 5"/></svg>
  <svg width="22" height="20" viewBox="0 0 22 20" fill="none" stroke="#fff" stroke-width="1.5"><path d="M1 2h3l3 11h11l2-8H6"/><circle cx="9" cy="17" r="1.5"/><circle cx="16" cy="17" r="1.5"/></svg>
  <span class="cart-badge">0</span>
</div>

<div class="abs hero-kicker">New Zealand</div>
<h1 class="abs hero-title">Taranaki<br>based manuka<br>honey...</h1>
<p class="abs hero-text">Export the highest quality quality Manuka Honey, straight from the Taranaki region.</p>
<div class="abs btn-gold">SHOP NOW</div>
<div class="abs vline" style="left:325px;top:567px;height:166px"></div>

<div class="photo" style="left:482px;top:133px;width:450px;height:534px;background:linear-gradient(160deg,#4d5a40,#8a8d80 45%,#c9c6bd 70%,#6c6a5e)" role="img" aria-label="Beekeeper in a white suit lifting a frame from a hive"></div>

<!-- About -->
<div class="abs about-band"></div>

<div class="abs frame-white" style="left:87px;top:931px;width:408px;height:570px"></div>
<div class="photo" style="left:102px;top:949px;width:380px;height:537px;background:linear-gradient(170deg,#3f8fb8 0%,#8d7a5a 35%,#4b4a38 70%,#2f3b33)" role="img" aria-label="Beekeepers tending hives among trees under a blue sky"></div>

<section class="abs about-card">
  <h2 class="abs about-title">About Rimu Vale Honey</h2>
  <div class="abs about-rule"></div>
  <p class="abs about-text">Aenean sollicitudin, lorem quis bibendum auctor, nisi elit consequat ipsum, nec sagittis sem nibh id elit. Duis sed odio sit amet nibh vulputate cursus a sit amet mauris. Morbi accumsan ipsum velit. Nam nec tellus a odio tincidunt auctor a ornare odio. Sed non &nbsp;mauris vitae erat consequat auctor eu in elit. Class aptent taciti sociosqu ad litora...</p>
  <div class="abs btn-grey">READ MORE</div>
</section>

<!-- Products -->
<div class="abs vline" style="left:835px;top:1475px;height:168px"></div>
<h2 class="abs section-title" style="top:1626px">Our Products</h2>

<div class="abs product" style="left:104px">
  <div class="jar" role="img" aria-label="Jar of honey"></div>
  <div class="product-name">01: Some product<br>heading goes here</div>
  <div class="stars">★★<span class="off">★★</span>★</div>
  <div class="product-rule"></div>
  <div class="price">Price: <b>$25.00</b></div>
</div>
<div class="abs product" style="left:355px">
  <div class="jar" role="img" aria-label="Jar of honey"></div>
  <div class="product-name">01: Some product<br>heading goes here</div>
  <div class="stars">★<span class="off">★★★</span>★</div>
  <div class="product-rule"></div>
  <div class="price">Price: <b>$25.00</b></div>
</div>
<div class="abs product" style="left:607px">
  <div class="jar" role="img" aria-label="Jar of honey"></div>
  <div class="product-name">01: Some product<br>heading goes here</div>
  <div class="stars">★★★★★</div>
  <div class="product-rule"></div>
  <div class="price">Price: <b>$25.00</b></div>
</div>
<div class="abs product" style="left:858px">
  <div class="jar" role="img" aria-label="Jar of honey"></div>
  <div class="product-name">01: Some product<br>heading goes here</div>
  <div class="stars">★★<span class="off">★</span>★★</div>
  <div class="product-rule"></div>
  <div class="price">Price: <b>$25.00</b></div>
</div>

<!-- MGO / KPS -->
<div class="abs vline" style="left:325px;top:2137px;height:165px"></div>
<h2 class="abs section-title" style="top:2156px">What is MGO/KPS</h2>

<div class="photo" style="left:599px;top:2262px;width:512px;height:617px;background:linear-gradient(150deg,#7a6a55,#c48a1c 35%,#8a7257 60%,#5b4c3d)" role="img" aria-label="Jar of honey and wooden spoon with a honey dipper on a rustic table"></div>

<section class="abs mgo-card">
  <h3 class="abs mgo-heading">How the ratings comapare KPS vs MGO</h3>
  <p class="abs mgo-text">Aenean sollicitudin, lorem quis bibendum auctor, nisi elit consequat ipsum, nec sagittis sem nibh id elit..</p>
  <table class="grade-table">
    <tr><td>KPS 05</td><td>MGO89</td></tr>
    <tr><td>KPS 10</td><td>MGO263</td></tr>
    <tr><td>KPS 15</td><td>MGO514</td></tr>
    <tr><td>KPS 20</td><td>MGO829</td></tr>
    <tr><td>KPS 25</td><td>MGO1200</td></tr>
  </table>
</section>
<div class="abs vs">VS</div>

<div class="abs arrow-btn" style="left:162px;top:2836px"><svg width="16" height="12" viewBox="0 0 16 12" fill="none" stroke="#cfcfcf" stroke-width="1.5"><path d="M15 6H2M6 1L1 6l5 5"/></svg></div>
<div class="abs slider-rule"></div>
<div class="abs arrow-btn" style="left:484px;top:2836px"><svg width="16" height="12" viewBox="0 0 16 12" fill="none" stroke="#cfcfcf" stroke-width="1.5"><path d="M1 6h13M10 1l5 5-5 5"/></svg></div>

<!-- Video -->
<div class="photo" style="left:175px;top:3040px;width:395px;height:470px;background:linear-gradient(160deg,#3a3326,#7a5b2c 40%,#b7a58a 70%,#d5d0c6)" role="img" aria-label="Gloved hands lifting a honeycomb frame from a hive"></div>
<div class="abs frame-white" style="left:86px;top:3313px;width:274px;height:285px"></div>
<div class="photo" style="left:96px;top:3323px;width:254px;height:265px;background:linear-gradient(160deg,#3d5a34,#cfcfc6 50%,#6f7f5e)" role="img" aria-label="Beekeeper in protective suit working at a hive"></div>
<div class="abs play"><svg width="26" height="28" viewBox="0 0 26 28"><path d="M3 2l21 12L3 26z" fill="#2b2b2b"/></svg></div>

<h2 class="abs video-title">Rimu Vale Honey video</h2>
<div class="abs video-text">
  <p>Aenean sollicitudin, lorem quis bibendum auctor, nisi elit amet nibh vulputate cursus a sit amet mauris cumsan ipsum velit. Nam nec tellus a odio tincidunt auctor a ornare odio. Sed non &nbsp;mauris vitae...</p>
  <p style="margin-top:22px">Litora torquent per conubia nostra, per inceptos himenaeos. Mauris in erat justo. Nullam ac urna eu felis dapibus mentum sit amet a augue.</p>
</div>

<!-- Newsletter & footer -->
<div class="abs footer-bg"></div>
<section class="abs newsletter">
  <div class="abs newsletter-label">JOIN OUR MAILING LIST</div>
  <div class="abs newsletter-field">
    <svg width="16" height="12" viewBox="0 0 16 12"><rect x="0" y="0" width="16" height="12" rx="1.5" fill="#9a9a9a"/><path d="M1 1l7 6 7-6" stroke="#fff" stroke-width="1.3" fill="none"/></svg>
    Enter your email address
    <div class="subscribe">SUBSCRIBE</div>
  </div>
</section>

<div class="abs footer-brand">Rimu Vale<br>Honey</div>

<div class="abs footer-col" style="left:439px;top:3872px">
  <h4>Information</h4>
  <a>About us</a>
  <a style="margin-top:8px">FAQ</a>
  <a style="margin-top:8px">Partnership Inquiries</a>
</div>
<div class="abs footer-col" style="left:664px;top:3872px">
  <h4>Let us help</h4>
  <a>Privacy Policy</a>
  <a style="margin-top:11px">Return Policy</a>
  <a style="margin-top:11px">Terms &amp; Condition</a>
  <a style="margin-top:11px">Contact us</a>
  <a style="margin-top:11px">FAQ's</a>
</div>
<div class="abs footer-col" style="left:869px;top:3872px">
  <h4>Follow Us</h4>
</div>
<div class="abs social" style="left:865px;top:3916px" aria-label="Social profile"></div>
<div class="abs social" style="left:907px;top:3916px" aria-label="Social profile"></div>
<div class="abs social" style="left:950px;top:3916px" aria-label="Social profile"></div>
<div class="abs social" style="left:993px;top:3916px" aria-label="Social profile"></div>

<div class="abs footer-rule"></div>
<div class="abs to-top"><svg width="12" height="14" viewBox="0 0 12 14" fill="none" stroke="#2b2b2b" stroke-width="1.5"><path d="M6 13V2M1 6l5-5 5 5"/></svg></div>
<div class="abs copyright">©2021 ABOUT RIMU VALE HONEY. ALL RIGHTS RESERVED</div>

</body>
</html>
```